Website for Torvel Capital - investment banking firm

We have a corporate identity (thanks to Ravinka/31842) and want to extend that into a website design.  See the attached zipped files.
We have software folks in-house to do the coding.
See the attached Project Brief & Notes for more details.  Don't worry about the actual text - lorem ipsum will be fine.
The server will be Apache.
Thank you!
Desmond

Industry/Entity Type
Investment

```html
<!DOCTYPE html>
<html lang="en">
<head>
<meta charset="utf-8">
<title>Torvel Capital</title>
<link rel="stylesheet" href="https://fonts.googleapis.com/css2?family=Figtree:wght@400;500;700&family=Open+Sans:wght@400&display=swap">
<style>
  :root {
    --brand-blue: #1c4a8c;
    --ink: #1a1a1a;
    --muted: #555;
    --rule: #d6d6d6;
    --white: #ffffff;
    --search-btn: #8f9399;
  }
  * { box-sizing: border-box; margin: 0; padding: 0; }
  html, body { width: 1200px; height: 768px; overflow: hidden; background: var(--white); }
  body { position: relative; font-family: "Figtree", Arial, sans-serif; color: var(--ink); }

  .brand { position: absolute; left: 118px; top: 38px; display: flex; align-items: center; gap: 14px; }
  .brand-mark { width: 50px; height: 50px; border-radius: 50%; background: var(--brand-blue); }
  .brand-name { font-size: 30px; font-weight: 500; color: var(--brand-blue); letter-spacing: .5px; }

  .utility-nav { position: absolute; right: 123px; top: 39px; display: flex; gap: 20px; font-size: 13px; text-transform: uppercase; white-space: nowrap; }
  .utility-nav a { color: var(--ink); text-decoration: none; }
  .utility-nav .sep { color: var(--muted); font-size: 11px; }
  .call-line { position: absolute; right: 123px; top: 67px; font-size: 21px; color: var(--brand-blue); white-space: nowrap; }

  .main-nav { position: absolute; left: 120px; top: 125px; width: 960px; height: 40px; background: var(--brand-blue); display: flex; align-items: center; padding-left: 23px; }
  .main-nav ul { list-style: none; display: flex; align-items: center; white-space: nowrap; }
  .main-nav li { color: var(--white); font-size: 13px; font-weight: 500; }
  .main-nav li.sep { font-size: 10px; margin: 0 18px; }
  .search { position: absolute; right: 15px; top: 7px; display: flex; }
  .search-field { width: 139px; height: 23px; background: var(--white); font-size: 11px; color: #999; padding: 5px 8px; white-space: nowrap; }
  .search-btn { width: 24px; height: 23px; background: var(--search-btn); display: flex; align-items: center; justify-content: center; }

  .hero { position: absolute; left: 121px; top: 165px; width: 959px; height: 501px; }
  .hero-photo { position: absolute; inset: 0; background: linear-gradient(160deg, #c9c4c6 0%, #e9d3b6 30%, #f4d7a6 45%, #b9a594 60%, #5f6c86 80%, #435272 100%); }
  .hero-title { position: absolute; left: 541px; top: 58px; font-size: 26.5px; line-height: 34px; font-weight: 400; color: var(--ink); white-space: nowrap; }
  .hero-cta { position: absolute; left: 543px; top: 140px; width: 126px; height: 31px; background: var(--brand-blue); color: var(--white); font-size: 14px; font-weight: 700; display: flex; align-items: center; justify-content: center; text-transform: uppercase; }

  .services { position: absolute; left: 34px; top: 368px; display: flex; gap: 6px; }
  .service-card { width: 216px; height: 83px; background: var(--white); padding: 13px 12px 0 15px; overflow: hidden; }
  .service-card h3 { font-size: 13px; font-weight: 700; color: var(--brand-blue); text-transform: uppercase; letter-spacing: 0; white-space: nowrap; margin-bottom: 8px; line-height: 16px; }
  .service-card p { font-family: "Open Sans", Arial, sans-serif; font-size: 10.8px; line-height: 15px; color: var(--ink); white-space: nowrap; letter-spacing: -0.1px; }

  .footer { position: absolute; left: 121px; top: 689px; width: 959px; border-top: 1px solid var(--rule); }
  .footer-links { position: absolute; left: 4px; top: 16px; display: flex; gap: 20px; font-size: 13px; color: #444; letter-spacing: .3px; white-space: nowrap; }
  .copyright { position: absolute; right: 12px; top: 18px; font-size: 12.5px; color: #444; letter-spacing: .4px; white-space: nowrap; }
</style>
</head>
<body>
  <header>
    <div class="brand">
      <span class="brand-mark"></span>
      <span class="brand-name">Torvel Capital</span>
    </div>
    <nav class="utility-nav">
      <a href="#">Home</a><span class="sep">|</span>
      <a href="#">Sitemap</a><span class="sep">|</span>
      <a href="#">Contact Us</a>
    </nav>
    <div class="call-line">CALL US : 469.555.0187</div>
  </header>

  <nav class="main-nav">
    <ul>
      <li>Home</li><li class="sep">|</li>
      <li>About</li><li class="sep">|</li>
      <li>Services</li><li class="sep">|</li>
      <li>Current Engagements</li><li class="sep">|</li>
      <li>Completed Transactions</li>
    </ul>
    <div class="search">
      <div class="search-field">enter search term</div>
      <div class="search-btn">
        <svg width="8" height="9" viewBox="0 0 8 9"><polygon points="0,0 8,4.5 0,9" fill="#fff"/></svg>
      </div>
    </div>
  </nav>

  <section class="hero">
    <div class="hero-photo" role="img" aria-label="Sailboat deck with winches and ropes facing the sea at sunset"></div>
    <h1 class="hero-title">Progress is the Activity of Today<br>and the Assurance of Tomorrow</h1>
    <div class="hero-cta">Learn More</div>
    <div class="services">
      <div class="service-card"><h3>Strategic Advisory</h3><p>Lorem Ipsum is simply dummy text<br>of the printing and typesetting</p></div>
      <div class="service-card"><h3>Current Engagements</h3><p>Lorem Ipsum is simply dummy text<br>of the printing and typesetting</p></div>
      <div class="service-card"><h3>Completed Transaction</h3><p>Lorem Ipsum is simply dummy text<br>of the printing and typesetting</p></div>
      <div class="service-card"><h3>Regulatory Compliance</h3><p>Lorem Ipsum is simply dummy text<br>of the printing and typesetting</p></div>
    </div>
  </section>

  <footer class="footer">
    <div class="footer-links"><span>Home</span><span>Terms &amp; Conditions</span><span>Contact Us</span></div>
    <div class="copyright">© 2014 Torvel Capital. All Rights Reserved</div>
  </footer>
</body>
</html>
```